Business Card for premium dental clinic

We are a premium dental clinic based in Brasov, Romania with more than 15 year on the market, providing quality dental treatment made by a team of more specialized dentists, working with modern equipment as a solution to beautiful and healthy teeth.

Our current logo for the clinic use 2 square with colors black and gold - dr Ternisu - studio, using family fonts Bodoni, Myriad Pro and Segoe Print.
Depending on the printing we used some gold CMYK background or gold foil picture background or a gold gradient.
We want a business card:
- eye catching business card
- distinguished business card
- premium design
- to keep the color scheme of black and gold
- to attract the customers to spent time reading the information
- modern concept

```html
<!DOCTYPE html>
<html lang="en">
<head>
<meta charset="utf-8">
<title>dr Ternisu – Business Card</title>
<link rel="stylesheet" href="https://fonts.googleapis.com/css2?family=Mulish:wght@300;400;500&display=swap">
<style>
  :root {
    --ink: #222021;
    --gold: #e7b424;
    --gold-light: #f6cf4a;
    --gold-deep: #c98d12;
    --paper: #ffffff;
    --shadow: rgba(0, 0, 0, 0.28);
  }
  * { box-sizing: border-box; margin: 0; padding: 0; }
  html, body {
    width: 902px;
    height: 1200px;
    overflow: hidden;
    background: var(--paper);
    font-family: "Mulish", sans-serif;
  }
  .sheet { position: relative; width: 902px; height: 1200px; }

  .card {
    position: absolute;
    left: 77px;
    width: 757px;
    height: 435px;
    box-shadow: 3px 4px 5px var(--shadow);
    overflow: hidden;
    background: var(--paper);
  }
  .card--front { top: 131px; }
  .card--back { top: 631px; background: var(--ink); }

  .gold-foil {
    position: absolute;
    top: 0;
    background:
      radial-gradient(circle at 30% 25%, var(--gold-light) 0%, transparent 45%),
      radial-gradient(circle at 75% 80%, var(--gold-deep) 0%, transparent 50%),
      linear-gradient(135deg, var(--gold-light), var(--gold) 50%, var(--gold-deep));
  }

  /* Front: contact details */
  .contact-panel {
    position: absolute;
    left: 0; top: 0;
    width: 379px; height: 435px;
    background: var(--ink);
    color: var(--gold);
  }
  .contact-panel__name {
    position: absolute;
    left: 50px; top: 98px;
    font-size: 28px;
    font-weight: 400;
    letter-spacing: 0.3px;
    line-height: 1;
  }
  .contact-panel__role {
    position: absolute;
    left: 50px; top: 129px;
    font-size: 17px;
    font-weight: 300;
    line-height: 1;
  }
  .contact-panel__rule {
    position: absolute;
    left: 50px; top: 155px;
    width: 129px; height: 1px;
    background: var(--gold);
  }
  .contact-panel__address {
    position: absolute;
    left: 50px; top: 246px;
    font-size: 17px;
    font-weight: 300;
    line-height: 22px;
  }
  .contact-list {
    position: absolute;
    left: 50px; top: 334px;
    list-style: none;
    font-size: 17px;
    font-weight: 300;
  }
  .contact-list li {
    display: flex;
    align-items: center;
    height: 22px;
  }
  .contact-list svg { width: 13px; height: 13px; margin-right: 12px; fill: var(--gold); }

  .card--front .gold-foil { left: 383px; width: 374px; height: 435px; }

  .brand-mark {
    position: absolute;
    display: flex;
    align-items: center;
  }
  .brand-mark__name {
    font-weight: 400;
    color: var(--ink);
    white-space: nowrap;
  }
  .brand-mark__square {
    position: relative;
    background: var(--ink);
  }

  .card--front .brand-mark { left: 420px; top: 166px; }
  .card--front .brand-mark__name { font-size: 25px; margin-right: 14px; }
  .card--front .brand-mark__square { width: 150px; height: 142px; }

  .tagline {
    position: absolute;
    color: var(--gold);
    font-weight: 500;
    white-space: nowrap;
    line-height: 1;
  }
  .card--front .tagline { right: 14px; bottom: 14px; font-size: 17px; }

  /* Back */
  .card--back .gold-foil { left: 0; width: 355px; height: 435px; }
  .card--back .brand-mark { left: 42px; top: 176px; }
  .card--back .brand-mark__name { font-size: 62px; line-height: 1; }
  .card--back .tagline { right: 48px; top: 340px; font-size: 38px; }
</style>
</head>
<body>
<main class="sheet">

  <section class="card card--front" aria-label="Business card front">
    <div class="contact-panel">
      <h1 class="contact-panel__name">DR. TERNISU</h1>
      <p class="contact-panel__role">Dental specialist</p>
      <div class="contact-panel__rule"></div>
      <p class="contact-panel__address">12th floor, Carpati Road no<br>48 Tower BVRO</p>
      <ul class="contact-list">
        <li>
          <svg viewBox="0 0 24 24" aria-hidden="true"><path d="M6.6 10.8a15.1 15.1 0 0 0 6.6 6.6l2.2-2.2c.3-.3.7-.4 1-.2 1.1.4 2.3.6 3.6.6.6 0 1 .4 1 1V20c0 .6-.4 1-1 1C10.6 21 3 13.4 3 4c0-.6.4-1 1-1h3.5c.6 0 1 .4 1 1 0 1.3.2 2.5.6 3.6.1.3 0 .7-.2 1z"/></svg>
          0268415903
        </li>
        <li>
          <svg viewBox="0 0 24 24" aria-hidden="true"><path d="M2 5h20v14H2z M3.5 6.5v.4L12 13l8.5-6.1v-.4z" fill-rule="evenodd"/></svg>
          mara.ionescu@ternisudent.ro
        </li>
        <li>
          <svg viewBox="0 0 24 24" aria-hidden="true"><circle cx="12" cy="12" r="10"/><path d="M7 6c2 1 3 3 2 5s1 3 3 3 2 3 1 5M15 4c0 2 2 3 4 3" stroke="#222021" stroke-width="2" fill="none"/></svg>
          www.ternisudent.ro
        </li>
      </ul>
    </div>
    <div class="gold-foil" role="img" aria-label="Gold foil texture background"></div>
    <div class="brand-mark">
      <span class="brand-mark__name">dr Ternisu</span>
      <span class="brand-mark__square">
        <span class="tagline">dental clinic</span>
      </span>
    </div>
  </section>

  <section class="card card--back" aria-label="Business card back">
    <div class="gold-foil" role="img" aria-label="Gold foil texture background"></div>
    <div class="brand-mark">
      <span class="brand-mark__name">dr Ternisu</span>
    </div>
    <p class="tagline">dental clinic</p>
  </section>

</main>
</body>
</html>
```